Maple Hollow Pet Waste Alliance needs dog-centric 11"x17" flyer needed for a pet photo contest

We need a brochure for the Maple Hollow Pet Waste Alliance. They are holding a photo contest to encourage people to submit cute/funny photos of their dogs and sign a pledge to pick up pet waste.
The design should be eye catching and fun.
For a mockup, samples and specs, see the instructions attached or here:
https://slides.quorvendocs.example/deck/7KTmwPzaLRbvQeHsNyGdcXoFuJ29AtVk4EqiZrWnBhDx/view?start=false&loop=false&delayms=3000

Target Market(s)

Dog owners in the Richmond Virginia metro area

Industry/Entity Type

Pet

Requirements
Must have
• Photo of dog (see samples in attached brief)
• Use the Maple Hollow Pet Waste Alliance Logo
• Have placeholders for sponsor listing
Nice to have
• Allusion to great prizes in flashy text

```html
<!DOCTYPE html>
<html lang="en">
<head>
<meta charset="utf-8">
<title>Pups for Pure Creeks – Maple Hollow Pet Waste Alliance</title>
<link href="https://fonts.googleapis.com/css2?family=Catamaran:wght@400;500;600;700&display=swap" rel="stylesheet">
<style>
  :root {
    --stream-blue: #1a9ad6;
    --ink: #111111;
    --paper: #ffffff;
    --box-line: #b9b9b9;
    --coat-tan: #c98a4e;
    --coat-white: #ece9e4;
  }
  * { margin: 0; padding: 0; box-sizing: border-box; }
  html, body { width: 776px; height: 1200px; overflow: hidden; background: var(--paper); }
  body { font-family: "Catamaran", "Helvetica Neue", Arial, sans-serif; color: var(--ink); }
  .flyer { position: relative; width: 776px; height: 1200px; overflow: hidden; background: var(--paper); }

  .header-wave { position: absolute; left: 0; top: 0; width: 776px; height: 200px; }
  .header-title {
    position: absolute; left: 0; top: 70px; width: 776px; text-align: center;
    color: var(--paper); font-size: 58px; font-weight: 600; line-height: 1; letter-spacing: 0.2px;
  }

  .dog-photo {
    position: absolute; left: 350px; top: 292px; width: 426px; height: 690px;
    border-radius: 160px 0 0 0;
    background: radial-gradient(ellipse at 55% 28%, var(--coat-tan) 0%, #b9804a 30%, var(--coat-white) 58%, #f6f4f1 85%, var(--paper) 100%);
    z-index: 0;
  }

  .copy { position: absolute; left: 42px; z-index: 1; }
  .lead-in { top: 202px; font-size: 26px; font-weight: 500; line-height: 1.2; }
  .contest-name { top: 246px; left: 40px; font-size: 40px; font-weight: 500; color: var(--stream-blue); line-height: 1.2; white-space: nowrap; }
  .lead-out { top: 295px; font-size: 26px; font-weight: 500; line-height: 1.2; }

  .prize-pill {
    position: absolute; left: 0; top: 338px; width: 362px; height: 64px;
    background: var(--ink); border-radius: 0 32px 32px 0; z-index: 1;
  }
  .prize-pill span {
    position: absolute; left: 34px; top: 0; color: var(--paper);
    font-size: 62px; font-weight: 500; line-height: 1;
  }
  .prize-dot { position: absolute; left: 300px; top: 12px; width: 40px; height: 40px; border-radius: 50%; background: var(--stream-blue); }

  .for-dog { top: 436px; font-size: 30px; font-weight: 500; line-height: 1.2; }
  .pledge { top: 472px; font-size: 21px; font-weight: 500; line-height: 28px; width: 322px; }
  .how-to { top: 646px; font-size: 21px; font-weight: 500; line-height: 28px; left: 38px; }
  .web-address { top: 757px; left: 38px; font-size: 25px; font-weight: 500; line-height: 36px; color: var(--stream-blue); }
  .deadline { top: 862px; left: 38px; font-size: 22px; font-weight: 500; line-height: 28px; }

  .sponsors { position: absolute; left: 316px; top: 950px; z-index: 1; }
  .sponsors-label { font-size: 16px; font-weight: 500; line-height: 1; margin-bottom: 15px; }
  .sponsor-slots { display: flex; gap: 21px; margin-left: 4px; }
  .sponsor-slot { width: 82px; height: 85px; border: 1px solid var(--box-line); background: var(--paper); }

  .alliance-mark { position: absolute; left: 0; top: 1070px; width: 776px; height: 130px; }
  .alliance-dot { position: absolute; left: 64px; top: 20px; width: 84px; height: 84px; border-radius: 50%; background: var(--ink); }
  .alliance-name {
    position: absolute; left: 170px; top: 40px; color: var(--ink);
    font-size: 40px; font-weight: 600; line-height: 1; white-space: nowrap;
  }
</style>
</head>
<body>
<main class="flyer">
  <svg class="header-wave" viewBox="0 0 776 200" aria-hidden="true">
    <path d="M0 0 H776 V170 C750 188 725 188 700 170 C675 152 650 152 625 170 C600 188 575 188 550 170 C525 152 500 152 475 170 C450 188 425 188 400 170 C375 152 350 152 325 170 C300 188 275 188 250 170 C225 152 200 152 175 170 C150 188 125 188 100 170 C75 152 50 152 25 170 C15 177 7 180 0 180 Z" fill="var(--stream-blue)"/>
  </svg>
  <h1 class="header-title">Pups for Pure Creeks</h1>

  <div class="dog-photo" role="img" aria-label="Photo of a tan and white terrier with a black collar, tilting its head and holding one ear up"></div>

  <p class="copy lead-in">Enter the</p>
  <p class="copy contest-name">“Pups for Pure Creeks”</p>
  <p class="copy lead-out">photo contest and</p>

  <div class="prize-pill"><span>win gear</span><i class="prize-dot"></i></div>

  <p class="copy for-dog">for your dog.</p>
  <p class="copy pledge">Pledge to pick up pet waste and<br>protect clean water.<br>Ask your friends and family<br>to vote for your adorable dog<br>and win great prizes from our<br>sponsors.</p>
  <p class="copy how-to">Enter your cover dog in the<br>photo contest today!<br>Here’s how:<br>Visit</p>
  <p class="copy web-address">www.pawboard.example/<br>MapleHollowPetWasteAlliance</p>
  <p class="copy deadline">Submit your photo by<br>06/12/2015</p>

  <section class="sponsors">
    <p class="sponsors-label">Contest Sponsors include:</p>
    <div class="sponsor-slots">
      <div class="sponsor-slot"></div>
      <div class="sponsor-slot"></div>
      <div class="sponsor-slot"></div>
      <div class="sponsor-slot"></div>
    </div>
  </section>

  <footer class="alliance-mark">
    <span class="alliance-dot"></span>
    <p class="alliance-name">Maple Hollow Pet Waste Alliance</p>
  </footer>
</main>
</body>
</html>
```